HearthMile business card and stationary design

We are looking for a simple yet elegant design for our mortgage company business card and stationary.

The card should include:
Name (Marcus Pell)
Title (CEO)
Phone Number (555-555-0182)
Address (48 Birchwell Court, Suite 314, Fernholt Bay 00412)
Email (email@hearthmile.example)
"NMLS" i.e. (NMLS 61947)
"Company NMLS" (Company NMLS 274615)

Contact Information for Business Card

See above

```html
<!DOCTYPE html>
<html lang="en">
<head>
<meta charset="utf-8">
<title>HearthMile Business Card</title>
<link href="https://fonts.googleapis.com/css2?family=Montserrat:wght@400;600;700&display=swap" rel="stylesheet">
<style>
  :root {
    --navy: #1a2533;
    --blue: #27a3de;
    --ink: #2c3440;
    --paper: #ffffff;
    --backdrop: #e6e8eb;
  }
  * { margin: 0; padding: 0; box-sizing: border-box; }
  html, body { width: 1200px; height: 786px; overflow: hidden; }
  body {
    background: var(--backdrop);
    font-family: "Montserrat", Arial, sans-serif;
    display: flex;
    align-items: center;
    justify-content: center;
    gap: 40px;
  }
  .card {
    position: relative;
    width: 540px;
    height: 309px;
    overflow: hidden;
    box-shadow: 0 6px 18px rgba(0,0,0,0.18);
  }
  .card--front { background: var(--paper); color: var(--ink); }
  .card--back { background: var(--navy); }

  .brand {
    position: absolute;
    display: flex;
    align-items: center;
    gap: 10px;
    font-weight: 600;
    letter-spacing: -0.5px;
    white-space: nowrap;
  }
  .brand__mark { width: 12px; height: 12px; background: var(--blue); flex: none; }
  .card--front .brand { left: 50%; top: 48px; transform: translateX(-50%); font-size: 46px; color: var(--navy); }
  .card--back .brand { left: 50%; top: 50%; transform: translate(-50%, -50%); font-size: 54px; color: #ffffff; }

  .divider {
    position: absolute;
    left: 28px; right: 26px; top: 186px;
    height: 1px;
    background: var(--blue);
  }
  .person { position: absolute; left: 28px; top: 140px; }
  .person__name {
    font-size: 20px; font-weight: 700; color: var(--blue);
    text-transform: uppercase; letter-spacing: 0.5px; line-height: 1.1;
  }
  .person__title { font-size: 11px; margin-top: 2px; }

  .licence {
    position: absolute; right: 26px; top: 146px;
    text-align: right; font-size: 10.5px; line-height: 1.45;
  }
  .address {
    position: absolute; right: 26px; top: 196px;
    text-align: right; font-size: 10.5px; line-height: 1.45;
  }
  .contact {
    position: absolute; left: 28px; top: 198px;
    list-style: none; font-size: 11px; line-height: 1.6;
  }
  .contact li { display: flex; align-items: center; gap: 6px; }
  .contact svg { width: 9px; height: 9px; fill: none; stroke: var(--blue); stroke-width: 1.6; }

  .edge { position: absolute; bottom: 0; height: 8px; }
  .edge--navy { left: 0; width: 270px; background: var(--navy); }
  .edge--blue { right: 0; width: 270px; background: var(--blue); }
</style>
</head>
<body>
  <section class="card card--front" aria-label="Business card front">
    <div class="brand"><span class="brand__mark"></span>HearthMile</div>

    <div class="person">
      <p class="person__name">Marcus Pell</p>
      <p class="person__title">CEO</p>
    </div>

    <div class="licence">
      <p>NMLS 61947</p>
      <p>Company NMLS 274615</p>
    </div>

    <div class="divider"></div>

    <ul class="contact">
      <li>
        <svg viewBox="0 0 10 10"><path d="M2 1 L4 3 L3 4.5 Q4.5 6.5 5.5 7 L7 6 L9 8 L7.5 9.3 Q3 8.5 0.8 2.5 Z"/></svg>
        555-555-0182
      </li>
      <li>
        <svg viewBox="0 0 10 10"><rect x="1" y="2" width="8" height="6"/><path d="M1 2 L5 5.5 L9 2"/></svg>
        email@hearthmile.example
      </li>
    </ul>

    <div class="address">
      <p>48 Birchwell Court,</p>
      <p>Suite 314, Fernholt Bay 00412</p>
    </div>

    <div class="edge edge--navy"></div>
    <div class="edge edge--blue"></div>
  </section>

  <section class="card card--back" aria-label="Business card back">
    <div class="brand"><span class="brand__mark"></span>HearthMile</div>
  </section>
</body>
</html>
```